Business Card Design for a Software Startup

We'd like to have a business card design. We already have a logo. Basically what we need is a clean design with name, address, cellphone and phone numbers, e-mail and web site address (front) and a space on the back with our logo with the company name on the right side and some texts on the bottom.
We are a development and consulting company in Brazil with highly qualified team of professionals in Java, iOS and Android development and consulting.

Target Market(s)

CIO, IT managers of mid to big size companies

Industry/Entity Type

Business

```html
<!DOCTYPE html>
<html lang="en">
<head>
<meta charset="utf-8">
<title>NORVEK Business Cards</title>
<link rel="stylesheet" href="https://fonts.googleapis.com/css2?family=Open+Sans:wght@400;600;700&display=swap">
<style>
  :root {
    --backdrop: #e9e6e1;
    --card: #ffffff;
    --navy: #0d3a66;
    --blue: #1f6fb8;
    --sky: #3aa0e0;
    --ink: #3a3a3a;
    --rule: #d6d6d6;
    --font: "Open Sans", Arial, sans-serif;
  }
  * { box-sizing: border-box; margin: 0; padding: 0; }
  html, body { width: 1200px; height: 720px; overflow: hidden; }
  body {
    background: var(--backdrop);
    font-family: var(--font);
    position: relative;
  }
  .card {
    position: absolute;
    top: 200px;
    width: 560px;
    height: 320px;
    background: var(--card);
    box-shadow: 0 6px 18px rgba(0,0,0,0.18);
    overflow: hidden;
  }
  .card--front { left: 27px; }
  .card--back { left: 613px; }

  /* Front */
  .brand-block {
    position: absolute;
    left: 40px;
    top: 70px;
    width: 210px;
    display: flex;
    flex-direction: column;
    align-items: center;
    gap: 14px;
  }
  .brand-square {
    width: 96px;
    height: 96px;
    border-radius: 12px;
    background: linear-gradient(135deg, var(--sky), var(--navy));
  }
  .brand-name {
    font-weight: 700;
    font-size: 40px;
    color: var(--navy);
    letter-spacing: 1px;
    line-height: 1;
  }
  .divider {
    position: absolute;
    left: 282px;
    top: 40px;
    width: 1px;
    height: 210px;
    background: var(--rule);
  }
  .contact {
    position: absolute;
    left: 306px;
    top: 42px;
    color: var(--ink);
  }
  .contact__name {
    font-weight: 700;
    font-size: 22px;
    color: var(--navy);
    line-height: 1.1;
  }
  .contact__title { font-size: 13px; margin-bottom: 12px; }
  .contact__list { list-style: none; font-size: 13px; line-height: 20px; }
  .contact__list li { display: flex; align-items: center; gap: 6px; }
  .contact__list svg { width: 11px; height: 11px; flex: none; }
  .contact__address { font-size: 13px; line-height: 18px; margin-top: 14px; }
  .front-band { position: absolute; left: 0; bottom: 0; width: 560px; height: 80px; }

  /* Back */
  .back-name {
    position: absolute;
    left: 0; right: 0;
    top: 100px;
    text-align: center;
    font-weight: 700;
    font-size: 92px;
    color: var(--navy);
    letter-spacing: 2px;
    line-height: 1;
  }
  .back-web {
    position: absolute;
    left: 0; right: 0;
    bottom: 48px;
    text-align: center;
    font-size: 17px;
    letter-spacing: 4px;
    color: var(--ink);
  }
</style>
</head>
<body>
  <section class="card card--front" aria-label="Card front">
    <div class="brand-block">
      <div class="brand-square"></div>
      <div class="brand-name">NORVEK</div>
    </div>
    <div class="divider"></div>
    <div class="contact">
      <p class="contact__name">Your Name</p>
      <p class="contact__title">Title</p>
      <ul class="contact__list">
        <li>
          <svg viewBox="0 0 12 12"><path d="M2.5 1h2l1 2.5-1.3 1a6 6 0 0 0 3.3 3.3l1-1.3 2.5 1v2c0 .6-.4 1-1 1A10 10 0 0 1 1.5 2c0-.6.4-1 1-1z" fill="var(--ink)"/></svg>
          555-210-3344
        </li>
        <li>
          <svg viewBox="0 0 12 12"><rect x="3" y="0.5" width="6" height="11" rx="1" fill="none" stroke="var(--ink)" stroke-width="1.2"/><circle cx="6" cy="9.5" r="0.8" fill="var(--ink)"/></svg>
          555-867-1290
        </li>
        <li>
          <svg viewBox="0 0 12 12"><rect x="0.5" y="2" width="11" height="8" rx="1" fill="var(--ink)"/><path d="M1 2.5l5 4 5-4" fill="none" stroke="#fff" stroke-width="1"/></svg>
          yourname@norvek.com
        </li>
        <li>
          <svg viewBox="0 0 12 12"><circle cx="6" cy="6" r="5.2" fill="none" stroke="var(--ink)" stroke-width="1.1"/><ellipse cx="6" cy="6" rx="2.2" ry="5.2" fill="none" stroke="var(--ink)" stroke-width="1"/><path d="M1 6h10" stroke="var(--ink)" stroke-width="1"/></svg>
          www.norvek.com
        </li>
      </ul>
      <p class="contact__address">Door No. Street Name<br>City Name, State, Zip Code</p>
    </div>
    <svg class="front-band" viewBox="0 0 560 80" preserveAspectRatio="none" aria-hidden="true">
      <defs>
        <linearGradient id="bandNavy" x1="0" y1="0" x2="1" y2="0">
          <stop offset="0" stop-color="#0d3a66"/>
          <stop offset="1" stop-color="#1f5a9c"/>
        </linearGradient>
        <linearGradient id="bandSky" x1="0" y1="0" x2="1" y2="0">
          <stop offset="0" stop-color="#2a86cc"/>
          <stop offset="1" stop-color="#55b6ec"/>
        </linearGradient>
      </defs>
      <path d="M0 66 L300 66 L560 18 L560 80 L0 80 Z" fill="url(#bandNavy)"/>
      <path d="M280 70 L560 22 L560 32 L320 72 Z" fill="url(#bandSky)"/>
      <path d="M0 66 L300 66 L560 18 L560 22 L305 70 L0 70 Z" fill="#ffffff" opacity="0.25"/>
    </svg>
  </section>

  <section class="card card--back" aria-label="Card back">
    <div class="back-name">NORVEK</div>
    <div class="back-web">www.norvek.com</div>
  </section>
</body>
</html>
```